Veldmark Supplies Business Card

Professional business card that stand out to our potential customers. Front and back with clean modern design

Industry/Entity Type

Oil and gas

Contact Information for Business Card

Name, address, website , office phone and cell number

Requirements
Must have
• Editable files for each employee

```html
<!DOCTYPE html>
<html lang="en">
<head>
<meta charset="utf-8">
<title>Veldmark Supplies Business Card</title>
<link rel="stylesheet" href="https://fonts.googleapis.com/css2?family=Montserrat:wght@400;500;800&display=swap">
<style>
  :root {
    --backdrop: #4a4a4a;
    --card: #161616;
    --card-deep: #0c0c0c;
    --edge-blue: #0fb0d2;
    --brand-red: #ec1f26;
    --brand-blue: #0fb0d2;
    --text-light: #f2f2f2;
    --pattern-light: #9a9a9a;
  }
  * { box-sizing: border-box; margin: 0; padding: 0; }
  html, body { width: 1200px; height: 801px; overflow: hidden; }
  body {
    background: var(--backdrop);
    font-family: "Montserrat", Arial, sans-serif;
    position: relative;
  }
  .card {
    position: absolute;
    top: 246px;
    width: 540px;
    height: 309px;
    border-radius: 16px;
    background: var(--card);
    border: 3px solid var(--edge-blue);
    overflow: hidden;
  }
  .card-front { left: 40px; }
  .card-back { left: 620px; }

  /* front */
  .brand {
    position: absolute;
    left: 30px;
    top: 0;
    width: 180px;
    height: 100%;
    display: flex;
    align-items: center;
    justify-content: center;
    gap: 10px;
  }
  .brand-square {
    width: 16px;
    height: 16px;
    background: var(--brand-blue);
    flex: none;
  }
  .brand-name {
    color: var(--brand-red);
    font-weight: 800;
    font-size: 19px;
    line-height: 1.15;
    text-transform: uppercase;
    letter-spacing: 0.5px;
  }
  .divider {
    position: absolute;
    left: 228px;
    top: 34px;
    width: 2px;
    height: 238px;
    background: var(--brand-red);
  }
  .details {
    position: absolute;
    left: 252px;
    top: 36px;
    color: var(--text-light);
  }
  .person-name {
    font-weight: 800;
    font-size: 27px;
    letter-spacing: 0.5px;
    line-height: 1;
  }
  .person-name .first { color: var(--brand-red); }
  .person-name .last { color: var(--brand-blue); }
  .person-role { font-size: 13px; margin-top: 6px; }
  .address { font-size: 12.5px; margin-top: 14px; line-height: 1.45; }
  .contacts { list-style: none; margin-top: 12px; font-size: 12.5px; line-height: 1.45; }
  .contacts li { display: flex; align-items: center; gap: 8px; }
  .contacts svg { width: 12px; height: 12px; flex: none; fill: var(--brand-red); }

  /* back */
  .back-pattern {
    position: absolute;
    inset: 0;
    background: linear-gradient(115deg, var(--pattern-light) 0%, #5a5a5a 30%, #262626 55%, var(--card-deep) 100%);
  }
</style>
</head>
<body>
  <section class="card card-front">
    <div class="brand">
      <span class="brand-square"></span>
      <span class="brand-name">Veldmark Supplies</span>
    </div>
    <div class="divider"></div>
    <div class="details">
      <h1 class="person-name"><span class="first">DALE</span> <span class="last">HORTON</span></h1>
      <p class="person-role">Managing Director</p>
      <p class="address">412 W.Ridgeline Suite 5<br>Midland, Tx 79701</p>
      <ul class="contacts">
        <li>
          <svg viewBox="0 0 12 12" aria-hidden="true"><path d="M2.5 0.8l2 2-1 1.3c.6 1.6 2 3 3.6 3.6l1.3-1 2 2-1.3 1.8C5.6 10.2 1.8 6.4 0.7 2.1z"/></svg>
          (555)610-0148
        </li>
        <li>
          <svg viewBox="0 0 12 12" aria-hidden="true"><path d="M3 0h6v12H3zM4 1.5v8h4v-8zM5.5 10.3h1v.9h-1z"/></svg>
          555 482 917
        </li>
        <li>
          <svg viewBox="0 0 12 12" aria-hidden="true"><path d="M0 2h12v8H0zM1 3l5 3.6L11 3v-.2H1z"/></svg>
          sales@veldmarksupplies.com
        </li>
        <li>
          <svg viewBox="0 0 12 12" aria-hidden="true"><circle cx="6" cy="6" r="5.5"/></svg>
          www.veldmarksupplies.com
        </li>
      </ul>
    </div>
  </section>

  <section class="card card-back">
    <div class="back-pattern" role="img" aria-label="Repeating brand mark pattern fading from silver to black"></div>
  </section>
</body>
</html>
```